Architectural, Engineering and Design Build

Tovandex4.com
Veteran Disabled Certified company is doing business in Architecture, Engineer and Design build - look simialr websites and come up with design follow following website
https://hollis-darnet.example/
https://www.venlorcogroup.example/
https://www.pembrisgc.example/contract-vehicles/service-disabled-veteran-owned-small-business-sdvosb/
https://www.corbelnetlink.example/about/sdvosb/

Target Market(s)

US - Defense and Federal Government

Industry/Entity Type

Colors
0054AA
0677BA
7BADD7
CADEEF
E8F1F8

Requirements
Must have
• Army, American patriotism , Buildings, construction, architecture, engineering
Nice to have
• I need to attract federal government agencies and Defense

```html
<!DOCTYPE html>
<html lang="en">
<head>
<meta charset="utf-8">
<title>Tovandex4 – Architectural Engineering Construction</title>
<link href="https://fonts.googleapis.com/css2?family=Outfit:wght@400;500;600;700;800&display=swap" rel="stylesheet">
<style>
:root{
  --blue:#0054AA;
  --blue-mid:#0677BA;
  --blue-soft:#7BADD7;
  --blue-pale:#CADEEF;
  --blue-mist:#E8F1F8;
  --navy:#1b2a42;
  --ink:#111;
  --text:#333;
  --white:#fff;
}
*{margin:0;padding:0;box-sizing:border-box}
html,body{width:1200px;height:4651px;overflow:hidden}
body{font-family:"Outfit",sans-serif;color:var(--ink);background:var(--white)}
.page{position:relative;width:1200px;height:4651px;overflow:hidden}
.abs{position:absolute}
.shapes{position:absolute;left:0;top:0}

/* header */
.brand{position:absolute;left:140px;top:50px;display:flex;align-items:center;gap:8px;color:var(--white);font-weight:700;font-size:24px;letter-spacing:1px}
.brand .dot{width:14px;height:14px;border-radius:50%;background:var(--white)}
.nav{position:absolute;top:46px;left:518px;display:flex;align-items:center;font-size:15px;color:var(--white)}
.nav a{color:var(--white);text-decoration:none;margin-right:40px}
.nav .btn-contact{margin:0 0 0 -10px;background:var(--white);color:var(--blue);border-radius:22px;padding:10px 34px;font-weight:500}
.vertical-name{position:absolute;left:54px;top:96px;display:flex;flex-direction:column;gap:14px;color:rgba(255,255,255,.35);font-size:30px;font-weight:400;text-align:center}
.hero-title{position:absolute;left:141px;top:196px;color:var(--white);font-size:33px;font-weight:700;line-height:48px}
.hero-text{position:absolute;left:141px;top:302px;width:370px;color:var(--white);font-size:14px;line-height:28px}
.btn-light{position:absolute;left:142px;top:402px;background:var(--white);color:var(--blue);border-radius:22px;font-size:13px;font-weight:500;padding:11px 30px}
.scroll{position:absolute;left:930px;top:448px;color:var(--white);font-size:13px;font-weight:600;text-align:center;width:54px}
.scroll i{display:block;margin:0 auto 10px;width:1px;height:80px;background:var(--white)}

h2.section{font-size:32px;font-weight:700;text-transform:uppercase;color:var(--ink)}
.lead{font-size:15px;line-height:24px;color:var(--text)}

.photo{position:absolute}
.card-cap{position:absolute;left:22px;bottom:28px;right:18px;color:var(--white);font-size:12px;line-height:19px}

.list-title{font-size:16px;font-weight:600;margin:0 0 14px}
.arrow-list{list-style:none}
.arrow-list li{display:flex;align-items:center;gap:10px;font-size:13px;color:var(--text);height:40px}

.why-title{position:absolute;top:1778px;left:0;width:1200px;text-align:center;color:var(--white);font-size:30px;font-weight:700}
.why-lead{position:absolute;top:1824px;left:355px;width:490px;text-align:center;color:var(--white);font-size:12px;line-height:20px}
.feature{position:absolute;top:1903px;width:260px;text-align:center;color:var(--white)}
.feature .ring{width:102px;height:102px;border:2px solid var(--white);border-radius:50%;margin:0 auto 22px;display:flex;align-items:center;justify-content:center}
.feature h3{font-size:15px;font-weight:600;margin-bottom:10px}
.feature p{font-size:11px;line-height:19px}

.about-h{position:absolute;left:141px;top:2504px;font-size:25px;font-weight:700;line-height:32px}
.about-p{position:absolute;left:141px;top:2581px;width:400px;font-size:14px;line-height:24px;color:var(--text)}
.mission{position:absolute;left:141px;top:2702px;font-size:18px;font-weight:600}
.mission-list{position:absolute;left:141px;top:2742px;display:flex;gap:36px;font-size:12px;color:var(--text)}
.mission-list span{display:flex;align-items:center;gap:8px}
.btn-blue{position:absolute;background:var(--blue);color:var(--white);border-radius:22px;font-size:14px;font-weight:500;padding:11px 20px}

.member{position:absolute;top:3050px;width:222px;text-align:center}
.member .avatar{width:222px;height:222px;border-radius:50%}
.member b{display:block;margin-top:22px;font-size:12px;font-weight:600}
.member span{display:block;font-size:11px;color:var(--text);margin-top:8px}
.circle-btn{position:absolute;width:58px;height:58px;border-radius:50%;display:flex;align-items:center;justify-content:center}
.circle-btn.light{background:var(--blue-mist)}
.circle-btn.dark{background:var(--blue)}

.testimonial{position:absolute;top:3520px;width:444px;height:274px;border-radius:24px;padding:60px 28px 0}
.testimonial.alt{background:var(--blue-mist)}
.testimonial.plain{background:var(--white);box-shadow:0 4px 18px rgba(0,0,0,.12)}
.testimonial p{font-size:16px;line-height:28px;color:var(--text)}
.quote-badge{position:absolute;top:-26px;left:64px;width:58px;height:58px;border-radius:14px;background:var(--blue);display:flex;align-items:center;justify-content:center;color:var(--white);font-size:48px;font-weight:800;line-height:1}
.author{display:flex;align-items:center;gap:18px;margin-top:22px}
.author .pic{width:78px;height:78px;border-radius:50%}
.author b{display:block;font-size:22px;font-weight:600;color:#444}
.author small{font-size:13px;color:var(--text)}

.cta-title{position:absolute;top:3962px;left:0;width:1200px;text-align:center;font-size:26px;font-weight:700}
.cta-text{position:absolute;top:4014px;left:0;width:1200px;text-align:center;font-size:13px;font-weight:500}

.footer-col{position:absolute;color:var(--white)}
.footer-col h4{font-size:23px;font-weight:700;margin-bottom:22px}
.footer-col a{display:block;color:var(--white);text-decoration:none;font-size:14px;font-weight:500;margin-bottom:22px}
.info-row{display:flex;gap:14px;align-items:flex-start;font-size:14px;font-weight:500;line-height:22px;margin-bottom:24px}
.footer-brand{position:absolute;left:828px;top:4355px;display:flex;align-items:center;gap:10px;color:var(--white);font-size:36px;font-weight:700}
.footer-brand .dot{width:22px;height:22px;border-radius:50%;background:var(--white)}
.footer-tag{position:absolute;left:780px;top:4466px;width:296px;text-align:center;color:var(--white);font-size:13px;font-weight:500}
.social{position:absolute;top:4506px;width:32px;height:32px;border:1.5px solid var(--white);border-radius:50%}
.copyright{position:absolute;left:0;top:4585px;width:1200px;height:66px;background:var(--blue);color:var(--white);font-size:12px;text-align:center;line-height:66px}
</style>
</head>
<body>
<div class="page">

  <svg class="shapes" width="1200" height="4651" viewBox="0 0 1200 4651">
    <defs>
      <linearGradient id="heroGrad" x1="0" y1="0" x2="1" y2="1">
        <stop offset="0" stop-color="#2b3440"/><stop offset=".5" stop-color="#4a5562"/><stop offset="1" stop-color="#252c36"/>
      </linearGradient>
      <linearGradient id="whyGrad" x1="0" y1="0" x2="0" y2="1">
        <stop offset="0" stop-color="#1d2b44"/><stop offset="1" stop-color="#2a3a57"/>
      </linearGradient>
      <linearGradient id="footGrad" x1="0" y1="0" x2="1" y2="0">
        <stop offset="0" stop-color="#17253d"/><stop offset="1" stop-color="#22324f"/>
      </linearGradient>
    </defs>
    <g role="img" aria-label="Hero photograph: armoured tank and soldiers advancing through smoke">
      <polygon points="0,0 1200,0 1200,540 840,640 0,541" fill="url(#heroGrad)"/>
    </g>
    <polygon points="0,541 840,640 1200,540 1200,556 840,658 0,578" fill="var(--blue)"/>
    <polygon points="310,2230 980,2230 1200,2380 1200,3330 0,3330 0,2500" fill="var(--blue-mist)"/>
    <polygon points="980,2230 1200,2230 1200,2380" fill="#f2f7fb"/>
    <g role="img" aria-label="Background photograph: grand arched hall with American flags">
      <polygon points="0,1745 361,1652 1200,1745 1200,2170 840,2262 0,2165" fill="url(#whyGrad)"/>
    </g>
    <polygon points="0,1718 361,1630 1200,1715 1200,1745 361,1652 0,1745" fill="var(--blue)"/>
    <polygon points="0,2165 840,2262 1200,2170 1200,2186 840,2280 0,2193" fill="var(--blue)"/>
    <rect x="0" y="3893" width="1200" height="340" fill="var(--blue-mist)"/>
    <g role="img" aria-label="Footer background photograph: flags and buildings in dark blue tint">
      <polygon points="0,4262 1200,4190 1200,4651 0,4651" fill="url(#footGrad)"/>
    </g>
    <polygon points="0,4225 1200,4158 1200,4190 0,4262" fill="var(--blue)"/>
  </svg>

  <!-- HERO -->
  <div class="brand"><span class="dot"></span>TOVANDEX4</div>
  <nav class="nav">
    <a href="#">Home</a><a href="#">About US</a><a href="#">Services</a><a href="#">Why Choose Us</a>
    <a href="#" class="btn-contact">Contact</a>
  </nav>
  <div class="vertical-name"><span>T</span><span>O</span><span>V</span><span>A</span><span>N</span><span>D</span><span>E</span><span>X</span><span>4</span></div>
  <h1 class="hero-title">BUILDING FOR THE FUTURE<br>OF DEFENSE</h1>
  <p class="hero-text">Pioneering the development of advanced, resilient, and<br>Sustainable defense infrastructure to meet<br>future challenges.</p>
  <div class="btn-light">Explore Our Services</div>
  <div class="scroll"><i></i>Scroll</div>

  <!-- SERVICES -->
  <h2 class="section abs" style="left:141px;top:735px">Our Services</h2>
  <p class="lead abs" style="left:141px;top:787px;width:560px">Lorem ipsum dolor sit amet, consectetur adipiscing elit, sed do eiusmod tempor aliqua Quis ipsum.</p>
  <div class="photo" role="img" aria-label="Photograph: red barn with American flag and musicians" style="left:142px;top:880px;width:454px;height:362px;background:linear-gradient(160deg,#9fb6c7 0%,#9a3b33 45%,#6d4b37 100%)"></div>
  <svg class="abs" style="left:658px;top:922px" width="62" height="76" viewBox="0 0 62 76" fill="none" stroke="#111" stroke-width="2.4">
    <rect x="2" y="2" width="50" height="70" rx="3"/><rect x="10" y="12" width="6" height="12"/><rect x="22" y="16" width="6" height="8"/><rect x="34" y="10" width="6" height="14"/>
    <rect x="10" y="34" width="8" height="8"/><line x1="24" y1="38" x2="42" y2="38"/><rect x="10" y="50" width="8" height="8"/><line x1="24" y1="54" x2="36" y2="54"/>
    <circle cx="50" cy="62" r="9" fill="#fff"/><circle cx="50" cy="62" r="3"/>
  </svg>
  <div class="abs" style="left:659px;top:1020px">
    <div class="list-title">Clear and concise descriptions</div>
    <ul class="arrow-list">
      <li><svg width="18" height="18" viewBox="0 0 18 18" fill="none" stroke="#111" stroke-width="1.8"><path d="M2 2 L16 9 L2 16 L6 9 Z"/></svg>Core architectural</li>
      <li><svg width="18" height="18" viewBox="0 0 18 18" fill="none" stroke="#111" stroke-width="1.8"><path d="M2 2 L16 9 L2 16 L6 9 Z"/></svg>Engineering</li>
      <li><svg width="18" height="18" viewBox="0 0 18 18" fill="none" stroke="#111" stroke-width="1.8"><path d="M2 2 L16 9 L2 16 L6 9 Z"/></svg>Design-build services</li>
      <li><svg width="18" height="18" viewBox="0 0 18 18" fill="none" stroke="#111" stroke-width="1.8"><path d="M2 2 L16 9 L2 16 L6 9 Z"/></svg>Defense and government sector</li>
    </ul>
  </div>
  <div class="photo" role="img" aria-label="Photograph: tall office tower with flags" style="left:142px;top:1301px;width:293px;height:228px;background:linear-gradient(180deg,#8fa3b8 0%,#5a5048 55%,#2e2b2b 100%)"><p class="card-cap">Lorem ipsum dolor sit amet, consectetur adipiscing elit, sed do.</p></div>
  <div class="photo" role="img" aria-label="Photograph: grand terminal hall with American flag" style="left:455px;top:1301px;width:292px;height:228px;background:linear-gradient(180deg,#a58a62 0%,#6b5440 55%,#2f2823 100%)"><p class="card-cap">Lorem ipsum dolor sit amet, consectetur adipiscing elit, sed do.</p></div>
  <div class="photo" role="img" aria-label="Photograph: domed government building under cloudy sky" style="left:766px;top:1301px;width:292px;height:228px;background:linear-gradient(180deg,#9aa7b5 0%,#6b6f72 55%,#2c2f33 100%)"><p class="card-cap">Lorem ipsum dolor sit amet, consectetur adipiscing elit, sed do.</p></div>

  <!-- WHY CHOOSE -->
  <h2 class="why-title">WHY CHOOSE US?</h2>
  <p class="why-lead">Lorem ipsum dolor sit amet, consectetur adipiscing elit, sed do eiusmod tempor aliqua Quis ipsum.</p>
  <div class="feature" style="left:144px">
    <div class="ring"><svg width="54" height="54" viewBox="0 0 54 54" fill="none" stroke="#fff" stroke-width="2"><circle cx="27" cy="18" r="10"/><path d="M6 40 L18 32 L27 38 L36 32 L48 40 M14 46 L27 38 L40 46"/></svg></div>
    <h3>Veteran-Owned Business</h3>
    <p>Lorem Ipsum is simply dummy text of the printing and typesetting industry. Lorem Ipsum has been the industry's ever</p>
  </div>
  <div class="feature" style="left:466px">
    <div class="ring"><svg width="54" height="54" viewBox="0 0 54 54" fill="none" stroke="#fff" stroke-width="2"><circle cx="27" cy="14" r="7"/><path d="M15 34 Q27 18 39 34"/><path d="M11 44 l3 -6 3 6 -6 -4 h6z M24 44 l3 -6 3 6 -6 -4 h6z M37 44 l3 -6 3 6 -6 -4 h6z"/></svg></div>
    <h3>Experience and Expertise</h3>
    <p>Lorem Ipsum is simply dummy text of the printing and typesetting industry. Lorem Ipsum has been the industry's ever</p>
  </div>
  <div class="feature" style="left:787px">
    <div class="ring"><svg width="54" height="54" viewBox="0 0 54 54" fill="none" stroke="#fff" stroke-width="2"><circle cx="30" cy="17" r="10"/><circle cx="30" cy="17" r="4"/><path d="M25 26 l-3 8 5 -2 3 4 M35 26 l3 8 -5 -2"/><path d="M6 38 Q16 34 24 40 L40 40 Q48 38 50 34 M6 46 L38 48"/></svg></div>
    <h3>Commitment to Quality</h3>
    <p>Lorem Ipsum is simply dummy text of the printing and typesetting industry. Lorem Ipsum has been the industry's ever</p>
  </div>

  <!-- ABOUT -->
  <h2 class="section abs" style="left:0;top:2362px;width:1200px;text-align:center">About Us</h2>
  <h3 class="about-h">TOVANDEX4 ARCHITECTURAL<br>ENGINEERING</h3>
  <p class="about-p">Lorem Ipsum is simply dummy text of the printing and typesetting industry. Lorem Ipsum has been the industry's standard dummy text ever since the 1500s, when an remaining essentially unchanged.</p>
  <div class="mission">Mission Statement</div>
  <div class="mission-list">
    <span><svg width="18" height="18" viewBox="0 0 18 18" fill="none" stroke="#111" stroke-width="1.8"><path d="M2 2 L16 9 L2 16 L6 9 Z"/></svg>Company's mission</span>
    <span><svg width="18" height="18" viewBox="0 0 18 18" fill="none" stroke="#111" stroke-width="1.8"><path d="M2 2 L16 9 L2 16 L6 9 Z"/></svg>Values</span>
  </div>
  <div class="btn-blue" style="left:142px;top:2798px">Read More</div>
  <div class="abs" style="left:662px;top:2436px;width:418px;height:430px;background:var(--white)"></div>
  <div class="photo" role="img" aria-label="Photograph: white domed capitol building under blue sky" style="left:606px;top:2457px;width:454px;height:443px;background:linear-gradient(180deg,#7da9d3 0%,#c7d8e6 45%,#b9b3a8 75%,#6f6a63 100%)"></div>

  <!-- TEAM -->
  <h2 class="abs" style="left:0;top:2970px;width:1200px;text-align:center;font-size:24px;font-weight:700">OUR TEAM</h2>
  <div class="circle-btn light" style="left:61px;top:3130px"><svg width="16" height="16" viewBox="0 0 16 16" fill="none" stroke="#333" stroke-width="2"><path d="M11 2 L5 8 L11 14"/></svg></div>
  <div class="circle-btn dark" style="left:1080px;top:3130px"><svg width="16" height="16" viewBox="0 0 16 16" fill="none" stroke="#fff" stroke-width="2"><path d="M5 2 L11 8 L5 14"/></svg></div>
  <div class="member" style="left:142px"><div class="avatar" role="img" aria-label="Team member portrait" style="background:linear-gradient(180deg,#c9c4bc,#3e5a72)"></div><b>Lorem ipsum dolor</b><span>Lorem ipsum dolor sit amet,</span></div>
  <div class="member" style="left:373px"><div class="avatar" role="img" aria-label="Team member portrait" style="background:linear-gradient(180deg,#b7b2aa,#2a2624)"></div><b>Lorem ipsum dolor</b><span>Lorem ipsum dolor sit amet,</span></div>
  <div class="member" style="left:606px"><div class="avatar" role="img" aria-label="Team member portrait" style="background:linear-gradient(180deg,#7d7872,#8a8c8f)"></div><b>Lorem ipsum dolor</b><span>Lorem ipsum dolor sit amet,</span></div>
  <div class="member" style="left:837px"><div class="avatar" role="img" aria-label="Team member portrait" style="background:linear-gradient(180deg,#b8b4ae,#e9e6e1)"></div><b>Lorem ipsum dolor</b><span>Lorem ipsum dolor sit amet,</span></div>

  <!-- TESTIMONIALS -->
  <h2 class="section abs" style="left:0;top:3405px;width:1200px;text-align:center">Client Testimonials</h2>
  <div class="circle-btn light" style="left:61px;top:3628px"><svg width="16" height="16" viewBox="0 0 16 16" fill="none" stroke="#333" stroke-width="2"><path d="M11 2 L5 8 L11 14"/></svg></div>
  <div class="circle-btn dark" style="left:1080px;top:3628px"><svg width="16" height="16" viewBox="0 0 16 16" fill="none" stroke="#fff" stroke-width="2"><path d="M5 2 L11 8 L5 14"/></svg></div>
  <div class="testimonial alt" style="left:142px">
    <div class="quote-badge">“</div>
    <p>Lorem ipsum dolor sit amet, consectetur adipisc-ing elit, sed do eiusmod tempor incididunt ut labore et dolore magna aliqua. Quis ipsum sus-</p>
    <div class="author"><div class="pic" role="img" aria-label="Client portrait" style="background:linear-gradient(180deg,#d9d3cb,#a33a2e)"></div><div><b>Tobin Marsh</b><small>Lorem Ipsum is simply</small></div></div>
  </div>
  <div class="testimonial plain" style="left:614px">
    <div class="quote-badge">“</div>
    <p>Lorem ipsum dolor sit amet, consectetur adipisc-ing elit, sed do eiusmod tempor incididunt ut labore et dolore magna aliqua. Quis ipsum sus-</p>
    <div class="author"><div class="pic" role="img" aria-label="Client portrait" style="background:linear-gradient(180deg,#d8b07a,#5a8fb0)"></div><div><b>Liorana</b><small>Lorem Ipsum is simply</small></div></div>
  </div>

  <!-- CTA -->
  <h2 class="cta-title">TOVANDEX4 ARCHITECTURAL ENGINEERING CONSTRUCTION</h2>
  <p class="cta-text">Lorem Ipsum is simply dummy text of the printing and typesetting industry.</p>
  <div class="btn-blue" style="left:510px;top:4050px;padding:11px 33px">Request A Quote</div>

  <!-- FOOTER -->
  <div class="footer-col" style="left:154px;top:4307px">
    <h4>Quick Links</h4>
    <a href="#">Home</a><a href="#">About Us</a><a href="#">Services</a><a href="#">Why Choose Us</a><a href="#">Contact</a>
  </div>
  <div class="footer-col" style="left:437px;top:4307px;width:300px">
    <h4>Contact Info</h4>
    <div class="info-row"><svg width="18" height="22" viewBox="0 0 18 22" fill="#fff"><path d="M9 0a8 8 0 0 0-8 8c0 6 8 14 8 14s8-8 8-14a8 8 0 0 0-8-8zm0 11a3 3 0 1 1 0-6 3 3 0 0 1 0 6z"/></svg><span>Lorem Ipsum is simply dummy text of the printing and typesetting industry</span></div>
    <div class="info-row"><svg width="18" height="18" viewBox="0 0 18 18" fill="#fff"><path d="M4 1l3 4-2 2c1 3 3 5 6 6l2-2 4 3-2 3C8 17 1 10 1 3z"/></svg><span>(123) 456-789</span></div>
    <div class="info-row"><svg width="18" height="14" viewBox="0 0 18 14" fill="none" stroke="#fff" stroke-width="1.8"><rect x="1" y="1" width="16" height="12"/><path d="M1 1 L9 8 L17 1"/></svg><span>info@tovandex4architectural.example</span></div>
  </div>
  <div class="footer-brand"><span class="dot"></span>TOVANDEX4</div>
  <div class="footer-tag">Architectural Engineering Construction</div>
  <div class="social" style="left:890px"></div>
  <div class="social" style="left:937px"></div>
  <div class="copyright">© 2024 Copyright Tovandex4 Architectural Engineering Construction. All Rights</div>

</div>
</body>
</html>
```